I need a business card design for a new business based in South West Australia.
I specialize in residential window cleaning & general handyman maintenance.

Dale Marsh - 412 SILVER HAWK DETAILING
- Window Cleaning
- House Maintenance

```html
<!DOCTYPE html>
<html lang="en">
<head>
<meta charset="UTF-8">
<title>412 Silver Hawk Detailing – Business Card</title>
<link rel="stylesheet" href="https://fonts.googleapis.com/css2?family=Open+Sans:wght@400;600&display=swap">
<style>
  :root {
    --backdrop: #2b2b2d;
    --card: #1d1d1f;
    --gold: #f4a612;
    --ink: #f2f2f2;
    --muted: #cfcfcf;
    --rule: #b07a1a;
  }
  * { margin: 0; padding: 0; box-sizing: border-box; }
  html, body { width: 1200px; height: 900px; overflow: hidden; }
  body {
    background: var(--backdrop);
    display: flex;
    align-items: center;
    justify-content: center;
    gap: 48px;
    font-family: "Open Sans", Arial, sans-serif;
  }
  .card {
    width: 525px;
    height: 300px;
    background: var(--card);
    border-radius: 22px;
    box-shadow: 0 10px 30px rgba(0,0,0,.45);
    position: relative;
  }
  /* Contact side */
  .card--contact { display: flex; align-items: center; }
  .brand-block {
    width: 262px;
    display: flex;
    flex-direction: column;
    align-items: center;
    gap: 14px;
  }
  .brand-dot {
    width: 96px; height: 96px; border-radius: 50%;
    background: var(--gold);
  }
  .brand-name {
    font-weight: 600;
    color: var(--gold);
    font-size: 17px;
    text-align: center;
    line-height: 1.25;
  }
  .divider {
    width: 1px; height: 190px;
    background: linear-gradient(var(--rule), transparent);
  }
  .details { padding-left: 26px; color: var(--ink); }
  .person-name { color: var(--gold); font-size: 20px; font-weight: 400; line-height: 1.1; }
  .person-role { font-size: 13px; color: var(--muted); margin-bottom: 14px; }
  .address { font-size: 13.5px; line-height: 1.35; margin-bottom: 14px; }
  .contact-list { list-style: none; font-size: 13.5px; line-height: 1.55; }
  .contact-list li { display: flex; align-items: center; gap: 9px; }
  .contact-list svg { width: 11px; height: 11px; fill: var(--gold); flex: none; }
  /* Name side */
  .card--logo {
    display: flex; flex-direction: column;
    align-items: center; justify-content: center; gap: 10px;
  }
  .logo-name {
    font-weight: 600;
    color: var(--gold);
    font-size: 27px;
  }
  .services {
    font-weight: 400;
    color: var(--muted);
    font-size: 14px;
  }
</style>
</head>
<body>
  <section class="card card--contact">
    <div class="brand-block">
      <div class="brand-dot"></div>
      <div class="brand-name">412 Silver Hawk<br>Detailing</div>
    </div>
    <div class="divider"></div>
    <div class="details">
      <p class="person-name">Dale Marsh</p>
      <p class="person-role">Managing Director</p>
      <p class="address">27 Karri Lane, Busselton<br>Western Australia, 6280.</p>
      <ul class="contact-list">
        <li><svg viewBox="0 0 16 16"><path d="M3.5 1l3 3-1.8 1.8c.9 2 2.5 3.6 4.5 4.5L11 8.5l3 3-2 2.5C6.5 13.5 2.5 9.5 1 3.5z"/></svg>0400 555 218</li>
        <li><svg viewBox="0 0 16 16"><path d="M1 3h14v10H1zM1 3l7 6 7-6" stroke="#1d1d1f" stroke-width="1.2"/></svg>hello@silverhawk.au</li>
        <li><svg viewBox="0 0 16 16"><path d="M6.5 9.5l3-3M5 8l-2 2a2.5 2.5 0 003.5 3.5l2-2M11 8l2-2A2.5 2.5 0 009.5 2.5l-2 2" fill="none" stroke="#f4a612" stroke-width="2"/></svg>www.silverhawk.au</li>
      </ul>
    </div>
  </section>

  <section class="card card--logo">
    <div class="logo-name">412 Silver Hawk Detailing</div>
    <div class="services">Window Cleaning · House Maintenance</div>
  </section>
</body>
</html>
```